Commercial Real Estate Corporate Site

Our company sells an ERP software to Commercial Real Estate Companies, this project is part of a marketing and sales relaunch of the company.

See attached for PDF formatted Design brief

The software is a modular system where client’s can adopt one module at a time. Our customers are corporate clients who own between 10M and 10B of real estate properties. The typical customer is from the IT or the Financial arm of the company. Our differentiation in the market is that our system is built on a no-code environment, so making changes for the client is quick. Incumbents in the market have long implementation cycles, and customization is often not possible. Competitors are Quorvel, TKB, PlotNest, Vumora.

We need a design for our site which will be implemented into Brevo Forge. **All designs must be compatible with the newest version of Brevo Forge.**

We have produced the following attached assets to use in the website design.:

1. Logo
2. Brand Guidelines
3. Content for Pages
4. Menu Structures
5. Illustrations (modules)
I can't attach them because the files are too big, so they're in this google drive instead:
https://files.examplestore.net/share/k29Xa7Lq0Pz3Rt8MwB5nYc4Hv1Jd6Fe?mode=view

The mechanic for our sales process is as follows:

1. We find on module from our application that a client is interested in. The illustrations that we’ve attached represent the individual modules (elements) of the software.
1. For instance, one of our current customers has purchased a commissions module from us which helps calculate the commission that brokers receive for buying and selling their properties.
2. We provide immense value through the module, and then keep in sales communication with the client to determine which other modules we can implement for them.
1. For instance, in the example above, the client is so happy with the commissions module that they want to start working with our leasing module as well. In the next business quarter, they also choose to add our financials module to their business systems.

### Logo

Attached

### Brand Guidelines

Attached

We are open to suggestions on the secondary colour palette.

### **Site Copy**

**We require the following pages to be created; For now, we will do one Market Page, one Product Page, and one Platform / Services Page, and we will use those as inspiration to create the other dozen Marketing Pages and 30 or so Product Pages.**

**Homepage**

Attached

**Market Page** - look at the quorvel site under the Office, Industrial, Retail (https://www.quorvel.com/products/quorvel-commercial-suite/)

**Product** - One product provided, but there will be 30 - look at the vumora page

(https://www.vumora.com/products/general-accounting)

**Platform / Services Page** - pages that tell the story of our platform and services, content to be provided - the platform will use our modules as it highlights the story of the configurability and composability of the platform. Instead of the icons that they use, we want to use our modules.

- https://www.pelbrix.com/enterprise-applications-platform
- https://www.pelbrix.com/cloud-architecture

**Team Page** - just add sample content for starters (6 Team Members to start)

**Schedule Demo Page** - the call to action for all pages

(https://go.vumora.com/schedule-demo.html)

### Menu Structure

The menu is provided as an attachment.

### Illustrations Information

A note about the illustrations - we have provided an illustrator file with the modules, and if you’d like you can arrange the in any way that you’d like to. We especially like when the modules are positioned like a periodic table of the elements.

Our existing clients are

- Torvane Coop - https://www.torvanecoop.com/real-estate/
- Dalsworth Realestate https://dalsworth.com

Our competitors are

- Quorvel - www.quorvel.com
- TKB - [www.tkbsoftware.com](https://www.tkbsoftware.com/) (we don’t like how this one looks)
- Vumora - www.vumora.com
- Plotnest - www.plotnest.com

Design inspiration

- https://lark-studio.brevosite.com/velmo
- Corporate
- Established
- Modern

### Stock Images Guidance

- https://www.drafta.net/design/QXR7Lm2TpWz/Hk9vN3c8Yd41-FbqsaZRr/edit?utm_content=QXR7Lm2TpWz&utm_campaign=designshare&utm_medium=link2&utm_source=sharebutton

Target Market(s)

Commercial Real Estate Companies - they typically own a portfolio of 50 - 5000 real estate properties and need a software to manage it all.

Coding

Coded - Design and coding required

Number of Pages Required

5+ page

Font styles to use
Other font styles liked:
• Fonts defined in brand guideline

Requirements
Must have
• Brevo Forge, Use the Elemental Design, Download ai.zip and png.zip Use Brand Guideline,
Nice to have
• Check design breif

```html
<!DOCTYPE html>
<html lang="en">
<head>
<meta charset="utf-8">
<title>Tessaro Logics — Enterprise Applications Platform</title>
<link href="https://fonts.googleapis.com/css2?family=Montserrat:wght@400;500;600;700&display=swap" rel="stylesheet">
<style>
  :root{
    --navy:#0b0a1e;
    --red:#e0141e;
    --white:#ffffff;
    --ink:#2b2b2b;
    --muted:#a3a3a3;
    --icon:#3d3d3d;
  }
  *{margin:0;padding:0;box-sizing:border-box}
  html,body{width:1200px;height:2484px;overflow:hidden}
  body{position:relative;background:var(--white);font-family:'Montserrat',sans-serif;color:var(--ink)}
  .abs{position:absolute}
  .hero-bg{left:0;top:0;width:1200px;height:620px;background:var(--navy)}
  .brand{font-weight:700;color:var(--red);display:flex;align-items:center;gap:6px}
  .brand .mark{width:14px;height:14px;background:var(--red);border-radius:3px}
  .nav-brand{left:75px;top:28px;font-size:20px}
  .nav{top:33px;left:413px;display:flex;gap:38px;font-size:12.5px;color:#9c9cae}
  .nav .active{color:var(--white);font-weight:600}
  .nav span svg{margin-left:3px;vertical-align:middle}
  .btn{display:flex;align-items:center;justify-content:center;font-size:15px;color:var(--red);border-radius:4px;background:var(--white)}
  .btn-outline{border:1px solid var(--red);background:transparent}
  .watch-demo{left:991px;top:15px;width:131px;height:50px}
  .hero-title{left:75px;top:145px;width:600px;font-size:31px;line-height:37px;font-weight:700;color:var(--white)}
  .hero-art{left:328px;top:81px;width:473px;height:286px;background:linear-gradient(135deg,#5a5a5a,#2a2a2a 55%,#cfcfcf);border-radius:6px;opacity:.85}
  .hero-copy{left:716px;top:151px;width:400px;font-size:16.5px;line-height:27px;color:var(--white)}
  .reach-out{left:716px;top:287px;width:156px;height:51px}
  .photo{}
  .band-1{left:78px;top:386px;width:981px;height:215px;background:linear-gradient(100deg,#dcdcd8 0%,#eeeeea 45%,#a9c6d4 60%,#c6d7df 100%)}
  .band-2{left:140px;top:601px;width:981px;height:216px;background:linear-gradient(100deg,#8fb3cb 0%,#b9c7cc 35%,#c9ccc9 60%,#a8aeb0 100%)}
  .modules-title{left:0;top:880px;width:1217px;text-align:center;font-size:34px;font-weight:600;color:#3a3a3a}
  .modules-sub{left:0;top:944px;width:1217px;text-align:center;font-size:16.5px;color:var(--muted)}
  .module{top:1007px;width:300px;text-align:center}
  .module .icon{width:60px;height:60px;border-radius:50%;background:var(--icon);margin:0 auto;display:flex;align-items:center;justify-content:center}
  .module h3{margin-top:18px;font-size:19.5px;font-weight:600;color:#3a3a3a}
  .module p{margin-top:20px;font-size:15px;line-height:24.5px;color:var(--muted);padding:0 8px}
  .module .detail{margin-top:16px;font-size:15px;font-weight:600;color:var(--ink);display:inline-flex;align-items:center;gap:6px}
  .about-photo{left:78px;top:1308px;width:383px;height:428px;background:linear-gradient(160deg,#9aa6b0 0%,#6d8f9a 45%,#5c8d98 100%)}
  .about-portrait{left:344px;top:1390px;width:235px;height:262px;background:linear-gradient(135deg,#e9dccd 0%,#c9a99a 50%,#7b4f55 100%)}
  .about-title{left:642px;top:1428px;font-size:20px;font-weight:600;color:#3a3a3a}
  .about-copy{left:642px;top:1470px;width:450px;font-size:15px;line-height:24.5px;color:var(--muted)}
  .learn-more{left:642px;top:1562px;width:116px;height:51px;border:1px solid var(--red)}
  .cta-bg{left:0;top:1773px;width:1200px;height:452px;background:var(--navy)}
  .cta-title{left:75px;top:1844px;width:680px;font-size:35px;line-height:42px;font-weight:600;color:var(--white)}
  .cta-copy{left:75px;top:1942px;width:590px;font-size:16.5px;line-height:27.2px;color:var(--white)}
  .download{left:75px;top:2100px;width:198px;height:50px}
  .cta-art{left:787px;top:1811px;width:338px;height:376px;background:linear-gradient(160deg,#ffffff 0%,#fbe3e4 50%,#f4b6b9 100%)}
  .foot-brand{left:131px;top:2262px;font-size:26px}
  .social{top:2322px;width:18px;height:18px;border-radius:50%;background:#2b2b2b}
  .foot-col{top:2246px;font-size:17px;color:#3a3a3a}
  .foot-col h4{font-size:17px;font-weight:600;margin-bottom:5px}
  .foot-col li{list-style:none;line-height:31px}
  .copyright{left:0;top:2445px;width:1200px;text-align:center;font-size:17px;color:#3a3a3a}
</style>
</head>
<body>
  <div class="abs hero-bg"></div>

  <div class="abs brand nav-brand"><span class="mark"></span>Tessaro</div>
  <nav class="abs nav">
    <span class="active">Home</span>
    <span>About<svg width="9" height="6" viewBox="0 0 9 6"><path d="M1 1l3.5 3.5L8 1" stroke="#9c9cae" fill="none" stroke-width="1.4"/></svg></span>
    <span>Modules<svg width="9" height="6" viewBox="0 0 9 6"><path d="M1 1l3.5 3.5L8 1" stroke="#9c9cae" fill="none" stroke-width="1.4"/></svg></span>
    <span>Platform<svg width="9" height="6" viewBox="0 0 9 6"><path d="M1 1l3.5 3.5L8 1" stroke="#9c9cae" fill="none" stroke-width="1.4"/></svg></span>
  </nav>
  <a class="abs btn btn-outline watch-demo">Watch Demo</a>

  <div class="abs hero-art" role="img" aria-label="Module blocks arranged like a periodic table"></div>
  <h1 class="abs hero-title">Welcome to Tessaro — an infinitely composable Enterprise Applications Platform (EAP) for real estate.</h1>
  <p class="abs hero-copy">The Tessaro Enterprise solution seamlessly delivers both modular software and bundled services to transform your business with less risk.</p>
  <a class="abs btn reach-out">Reach Out To Us</a>

  <div class="abs band-1" role="img" aria-label="White curved architecture against a pale blue sky"></div>
  <div class="abs band-2" role="img" aria-label="Sweeping white building facade under blue sky"></div>

  <h2 class="abs modules-title">The Modules of Tessaro</h2>
  <p class="abs modules-sub">In a laoreet purus. Integer turpis quam</p>

  <div class="abs module" style="left:99px">
    <div class="icon"><svg width="22" height="22" viewBox="0 0 22 22" fill="none" stroke="#fff" stroke-width="1.5"><path d="M11 4l8 4-8 4-8-4z"/><path d="M3 12l8 4 8-4"/></svg></div>
    <h3>Simple</h3>
    <p>Tessaro is the real estate industry’s only infinitely composable Enterprise Applications Platform (EAP)</p>
    <span class="detail">Detail<svg width="16" height="12" viewBox="0 0 16 12" fill="none" stroke="#2b2b2b" stroke-width="1.6"><path d="M1 6h13M9 1l5 5-5 5"/></svg></span>
  </div>
  <div class="abs module" style="left:449px">
    <div class="icon"><svg width="22" height="22" viewBox="0 0 22 22" fill="none" stroke="#fff" stroke-width="1.5"><rect x="6" y="10" width="10" height="9" rx="2"/><path d="M8 10V7a3 3 0 016 0v3"/><path d="M11 13v3"/></svg></div>
    <h3>Secure</h3>
    <p>Tessaro is the real estate industry’s only infinitely composable Enterprise Applications Platform (EAP)</p>
    <span class="detail">Detail<svg width="16" height="12" viewBox="0 0 16 12" fill="none" stroke="#2b2b2b" stroke-width="1.6"><path d="M1 6h13M9 1l5 5-5 5"/></svg></span>
  </div>
  <div class="abs module" style="left:800px">
    <div class="icon"><svg width="22" height="22" viewBox="0 0 22 22" fill="none" stroke="#fff" stroke-width="1.5"><rect x="4" y="4" width="14" height="14" rx="2"/><path d="M4 10l8-6M4 16L16 4M8 18l10-8M3 3l16 16"/></svg></div>
    <h3>Scalable</h3>
    <p>Tessaro is the real estate industry’s only infinitely composable Enterprise Applications Platform (EAP)</p>
    <span class="detail">Detail<svg width="16" height="12" viewBox="0 0 16 12" fill="none" stroke="#2b2b2b" stroke-width="1.6"><path d="M1 6h13M9 1l5 5-5 5"/></svg></span>
  </div>

  <div class="abs about-photo" role="img" aria-label="Curved tiled building facade against a teal sky"></div>
  <div class="abs about-portrait" role="img" aria-label="Smiling professional working at a laptop in an office"></div>
  <h3 class="abs about-title">About</h3>
  <p class="abs about-copy">Tessaro was born from decades of real estate enterprise software development and implementation experience — spanning hundreds of blue chip global real .</p>
  <a class="abs btn learn-more">Learn More</a>

  <div class="abs cta-bg"></div>
  <h2 class="abs cta-title">Feeling concerned about making the switch?</h2>
  <p class="abs cta-copy">Harwell Insights discovered that Vumora customers experience a 50% decrease in onboarding time for new members and an 80% decrease in time spent provisioning new users. Claim your complimentary copy of the complete study to uncover the comprehensive economic benefits Vumora can deliver to your.</p>
  <a class="abs btn download">Download The Report</a>
  <div class="abs cta-art" role="img" aria-label="Illustration of a person beside a large smartphone with app tiles"></div>

  <div class="abs brand foot-brand"><span class="mark" style="width:18px;height:18px"></span>Tessaro</div>
  <span class="abs social" style="left:133px" aria-label="Video channel"></span>
  <span class="abs social" style="left:166px" aria-label="Messaging channel"></span>

  <div class="abs foot-col" style="left:341px"><h4>Quick Link</h4><ul><li>Markets</li><li>Services</li><li>Events</li></ul></div>
  <div class="abs foot-col" style="left:575px"><h4>Solutions</h4><ul><li>All Solutions</li><li>Multifamily</li><li>Student</li></ul></div>
  <div class="abs foot-col" style="left:841px"><h4>Company</h4><ul style="margin-top:7px"><li>Summit</li><li>Resources</li><li>Blog</li></ul></div>

  <p class="abs copyright">Copyright © 2024 Tessaro Logics | All Rights Reserved</p>
</body>
</html>
```